2-Page Flyer for the Information Session about the Quiet Pathfinder Course

This is a flyer to announce/advertise an evening Information Session about the Quiet Pathfinder Course. This Program aims at mindfully rethinking and redesigning work (and life) for people who feel stuck or not entirely satisfied with their work and/or life (please see draft flyer attached for more details). This Program is property of Bright Meadow, a company that uses a combination of Mindfulness, Design, and Entrepreneurship to help people achieve greater happiness (in their work and lives).

Target Market(s)

People who feel stuck or not entirely satisfied with their work and/or life (please see draft flyer attached for more details)

Font styles to use
Serif
Sans Serif

Colors
ffffff
f37122
33a6d7
acd037

Requirements
Must have
• All of what I will say below is suggestive (I’m not a design expert), and I’m open to divert from it, if it makes sense and feels more interesting.
• I thought initially of a 2-page flyer (please see draft flyer attached). The first page could help people grasp the essence of the event quickly (in 1 or 2 minutes), and then, if they are interested/motivated, they would continue reading through page 2, which has more info about the Program in itself.
• Potential Structure
• Page 1
• . About the Information Session on the Quiet Pathfinder Course
• . Visible Date & Time, Contacts, Venue (and other relevant info)
• . About me (the facilitator)
• Page 2
• . About the Quiet Pathfinder Course
• I include a Powerpoint draft of the flyer with the content. The design is rudimentary and precarious from an aesthetics/organization point of view, and this is mainly where I need help (and maybe in other aspects too!).
• On the flyer, I would like to include:
• . A photo of myself (I attach 1 picture).
• . 1 or 2 beautiful-nature photos (cropped or full). One may have to do with looking at the sky, dreaming, and imagining a new work and life (2 photos with sky and clouds attached). The other has to do with walking the transformation journey (the photo with the person walking through the forest path).
• . bright meadow logo or logos (there are two slightly different ones, that can be used for different purposes). For the first page, I would like the bright meadow logo that has "bright meadow" written on the bottom, with the saying "Stillness, Craft and Venture for Bright Meadow" beneath. This is the main logo. For the 2nd page, you can choose the logo that adapts better.
• - Where it says the "the way out is in" it would be great to have a similar font to the one I attach (see file "Font_the_way_out_is_in.png" and Ankecallig-fg.ttf
Nice to have
• In terms of colours, I would not divert much from the logo colours (and of course white and black). I would like the flyer to be quite white. Almost like fairy-tale white: the white horse, the white snow, the white of the stars, the white heaven. White could be the base colour. White means peace, tranquillity, calm contentment, a smile.
• And then use the other colours. The green of the mindfulness. The blue of the sky, the dreams. And the orange of the sun, the energy, the fire, the action. And maybe the black for text.
• Where it says the "the way out is in" it would be great to have a similar font to the one I attach (see file "Font_the_way_out_is_in".
• I would like this flyer to be a piece of art, in every possible way. Simple, beautiful, ease, light, peaceful, calm happy. Just like the Quiet Pathfinder Course and bright meadow Company that I am creating intends to be. The mission of this Program and Company is to be a designer, a painter (a Picasso) of happier and more fulfilling human lives.
• I am very much looking forward to seeing your proposal(s).

```html
<!DOCTYPE html>
<html lang="en">
<head>
<meta charset="utf-8">
<title>Quiet Pathfinder Course – Information Session Flyer</title>
<link rel="stylesheet" href="https://fonts.googleapis.com/css2?family=Open+Sans:ital,wght@0,400;0,600;0,700;1,400;1,600&family=Oswald:wght@500;700&family=Caveat:wght@600&display=swap">
<style>
:root{
  --orange:#f37122;
  --blue:#33a6d7;
  --green:#acd037;
  --green-dark:#8fb526;
  --white:#ffffff;
  --ink:#222222;
  --grey:#9a9a9a;
  --stage:#d9d9d9;
  --panel:#f1f1f1;
}
*{box-sizing:border-box;margin:0;padding:0}
html,body{width:1200px;height:808px;overflow:hidden;background:var(--stage)}
body{position:relative;font-family:"Open Sans",Arial,sans-serif;color:var(--ink)}
.page{position:absolute;top:14px;width:553px;height:780px;background:var(--white);overflow:hidden}
.page--front{left:32px}
.page--back{left:615px}
.abs{position:absolute}

/* ---------- front ---------- */
.hero-sky{left:0;top:0;width:553px;height:397px;
  background:linear-gradient(180deg,#e9f1f7 0%,#c7dcec 30%,#8fb0c9 55%,#5f7f93 72%,#3e4d49 82%,#2b3430 100%)}
.hero-band{left:0;top:312px;width:553px;height:85px;background:rgba(25,30,28,.72)}
.brand-mark{left:257px;top:18px;width:40px;height:40px;border-radius:50%;background:var(--orange)}
.brand-name{left:0;width:553px;top:62px;text-align:center;font-size:22px;font-weight:400;color:var(--blue)}
.brand-tagline{left:0;width:553px;top:96px;text-align:center;font-size:8.5px;font-style:italic;font-weight:600}
.title{left:0;width:553px;text-align:center;font-family:"Oswald",sans-serif;font-weight:700;line-height:1;letter-spacing:-.5px}
.title--1{top:146px;font-size:42px;color:#2d2d2d}
.title--2{top:186px;font-size:44px;color:var(--orange)}
.title--3{top:226px;font-size:42px;color:var(--white)}
.session-pill{left:114px;top:275px;width:325px;height:31px;border-radius:16px;background:var(--orange);
  color:var(--white);font-weight:700;font-size:19px;text-align:center;line-height:31px}
.event-date{left:0;width:553px;top:316px;text-align:center;font-size:21px;color:var(--white);font-weight:700}
.event-date span{color:var(--blue);font-weight:400}
.event-time{left:0;width:553px;top:343px;text-align:center;font-size:20px;color:var(--orange)}
.event-venue{left:0;width:553px;top:369px;text-align:center;font-size:14px;color:var(--white);font-weight:600}
.event-venue span{color:var(--green);font-weight:400}
.intro{left:21px;width:512px;top:412px;font-size:9.3px;line-height:12px}
.section-head{left:21px;top:442px;font-size:14px;font-weight:600;color:var(--green-dark)}
.section-rule{left:150px;top:452px;width:383px;height:1px;background:var(--green)}
.who-text{left:21px;width:512px;top:465px;font-size:9.3px;line-height:12px}
.facilitator-panel{left:0;top:506px;width:553px;height:235px;background:var(--panel)}
.portrait{left:22px;top:560px;width:148px;height:148px;border-radius:50%;
  background:radial-gradient(circle at 50% 40%,#c9c3bf,#7d8790 70%,#5f6b74);border:3px solid var(--white)}
.fac-label{left:186px;top:522px;font-size:7.5px;font-style:italic;font-weight:600}
.fac-name{left:186px;top:532px;font-size:18px;font-weight:700;color:var(--orange)}
.fac-role{left:186px;top:554px;font-size:7.6px;font-style:italic;font-weight:600}
.fac-bio{left:186px;width:348px;top:568px;font-size:8.3px;line-height:11.6px;text-align:justify}
.fac-link{left:186px;top:713px;font-size:9.5px}
.fac-link b{color:var(--blue);font-weight:600}
.dot{display:inline-block;width:9px;height:9px;border-radius:50%;background:var(--blue);vertical-align:-1px;margin:0 3px}
.footer-bar{left:0;top:741px;width:553px;height:20px;background:var(--blue);color:var(--white);font-size:9.8px;line-height:20px}
.footer-bar .label{position:absolute;left:0;top:0;height:20px;width:136px;background:var(--white);
  color:var(--green-dark);font-style:italic;font-weight:600;padding-left:21px;border-radius:0 10px 10px 0}
.footer-bar .items{position:absolute;left:150px;top:0;white-space:nowrap}
.footer-bar .dot{background:var(--white)}

/* ---------- back ---------- */
.sky-header{left:0;top:0;width:553px;height:125px;background:linear-gradient(180deg,#a9cbe6 0%,#d3e5f3 55%,#e8f1f8 100%)}
.back-title{left:22px;top:18px;font-size:24px;font-weight:700;color:var(--orange)}
.back-intro{left:22px;width:512px;top:56px;font-size:9.6px;line-height:13.4px;font-style:italic}
.tab{height:21px;line-height:21px;color:var(--white);font-weight:700;font-size:15px;padding-left:20px}
.tab--program{left:0;top:146px;width:155px;background:var(--orange);border-radius:0 11px 11px 0}
.tab--why{left:0;top:375px;width:87px;background:var(--blue);border-radius:0 11px 11px 0}
.tab--how{left:275px;top:375px;width:76px;background:var(--green);border-radius:0 11px 11px 0;padding-left:16px}
.program-text{left:20px;width:240px;top:185px;font-size:9.5px;line-height:12.3px;text-align:justify}
.program-text p+p{margin-top:12px}
.cycle{left:278px;top:130px}
.how-rule{left:275px;top:395px;width:2px;height:210px;background:var(--green)}
.col-text{font-size:9.5px;line-height:12.3px;text-align:justify}
.why-text{left:21px;width:240px;top:410px}
.how-text{left:292px;width:240px;top:410px}
.steps{list-style:none;margin-top:8px}
.steps li{position:relative;padding-left:24px;margin-bottom:6px;text-align:left}
.steps li::before{content:attr(data-n);position:absolute;left:2px;top:1px;width:12px;height:12px;border-radius:50%;
  color:var(--white);font-size:8px;font-weight:700;text-align:center;line-height:12px}
.steps--why li::before{background:var(--blue)}
.steps--how li::before{background:var(--green)}
.forest{left:0;top:615px;width:553px;height:165px;background:linear-gradient(180deg,#3d3422 0%,#5a4a2c 35%,#6b6a38 60%,#2f2a1e 100%)}
.quote{left:168px;top:682px;font-family:"Caveat",cursive;font-size:34px;color:var(--white);line-height:1}
.quote-by{left:276px;top:724px;font-size:8.5px;font-style:italic;color:var(--orange)}
.back-mark{left:414px;top:700px;width:22px;height:22px;border-radius:50%;background:var(--orange)}
.back-name{left:441px;top:702px;font-size:15px;color:var(--blue);line-height:1}
.back-footer{left:0;top:743px;width:553px;height:19px;background:var(--blue);color:var(--white);font-size:9.6px;line-height:19px;text-align:center;white-space:nowrap}
.back-footer .dot{background:var(--white)}
</style>
</head>
<body>

<section class="page page--front" aria-label="Flyer front">
  <div class="abs hero-sky" role="img" aria-label="Photo of sky and clouds over a mountain range"></div>
  <div class="abs hero-band"></div>
  <div class="abs brand-mark"></div>
  <div class="abs brand-name">bright meadow</div>
  <div class="abs brand-tagline">Stillness, Craft and Venture for Bright Meadow</div>
  <div class="abs title title--1">QUIET</div>
  <div class="abs title title--2">PATHFINDER</div>
  <div class="abs title title--3">COURSE</div>
  <div class="abs session-pill">FREE INFORMATION SESSION</div>
  <div class="abs event-date"><span>Thursday</span> 5th September 2019</div>
  <div class="abs event-time">19:30 to 21:00</div>
  <div class="abs event-venue"><span>Venue:</span> Tidewater Coworking, C/ Almendro 42, Barcelona</div>

  <p class="abs intro">The purpose of this <b>free Information Session</b> is to give you a real insight into the <b>Quiet Pathfinder Course</b> and how it can help you make the most of your professional and personal life.</p>
  <h2 class="abs section-head">WHO CAN COME</h2>
  <div class="abs section-rule"></div>
  <p class="abs who-text">Whether you come on your own, or with friends or family, you'll be warmly welcomed. The session will take place on Thursday the 5th September 2019, from 19:30 to 21:00, at Tidewater Coworking. Please see information below to get in contact or to book a seat.</p>

  <div class="abs facilitator-panel"></div>
  <div class="abs portrait" role="img" aria-label="Portrait photo of the facilitator"></div>
  <div class="abs fac-label">Facilitator</div>
  <div class="abs fac-name">DR MARCO VIDAL</div>
  <div class="abs fac-role">Visiting Research Fellow, University of Aldermoor</div>
  <p class="abs fac-bio">Marco joined the University of Aldermoor School of Management as a Lecturer in Entrepreneurship in 2015. He completed his PhD in Entrepreneurship at Kelvingate Business School in 2014, receiving the prestigious Academy of Venture Studies' Doctoral Award. He began his business career as a Production Engineer for Voltaris, and later as a Sales Engineer for Norvek. After his MBA, he served as a Strategy Consultant for Ribeira Business School. Originally from Portugal, Marco enjoys designing and launching new ideas, international communities, mindfulness retreats, and musical improvisation. He nurtures a close connection to Willow Glen Mindfulness Centre, where he has practiced and volunteered over 9 months. He has a broad experience of sharing the benefits of mindfulness with others.</p>
  <div class="abs fac-link">More about the facilitator: <span class="dot"></span><b>www.netprofile.io/in/marcovidal</b></div>

  <div class="abs footer-bar">
    <span class="label">Information &amp; Booking</span>
    <span class="items"><span class="dot"></span> info@brightmeadow.io &nbsp;&nbsp;<span class="dot"></span> +34 600 000 412 <i>(video call and messaging)</i></span>
  </div>
</section>

<section class="page page--back" aria-label="Flyer back">
  <div class="abs sky-header" role="img" aria-label="Soft photo of blue sky and clouds"></div>
  <h1 class="abs back-title">What is Mindful Entrepreneurship</h1>
  <p class="abs back-intro">Being mindful means being aware and awake. Entrepreneurship is the creation of a new form of organising. Mindful Entrepreneurship is then the process of creating or redesigning your work and life with awareness, in a way that is reflective of you, of your passions and values, thus conducing to a greater sense of fulfilment and happiness.</p>

  <h2 class="abs tab tab--program">THE PROGRAM</h2>
  <div class="abs program-text">
    <p><b>The Quiet Pathfinder Course</b> is a <b>4-month long transformative journey</b> designed for people who feel stuck or not entirely satisfied with their professional and/or personal life. It will be of benefit for everyone, at any stage.</p>
    <p>The Program entails a five-hour workshop each month, complemented by two-hour weekly peer support meetings. It combines mindfulness techniques, design thinking methodology, and entrepreneurship frameworks.</p>
  </div>

  <svg class="abs cycle" width="275" height="230" viewBox="0 0 275 230" aria-label="Four workshops linked by weekly peer support meetings">
    <defs>
      <marker id="arrowhead" markerWidth="6" markerHeight="6" refX="4" refY="3" orient="auto">
        <path d="M0,0 L6,3 L0,6 z" fill="#9fc7e0"/>
      </marker>
    </defs>
    <g fill="none" stroke="#9fc7e0" stroke-width="1.2" marker-end="url(#arrowhead)">
      <path d="M163,56 Q192,64 200,88"/>
      <path d="M210,160 Q206,178 192,186"/>
      <path d="M80,190 Q63,184 56,166"/>
      <path d="M56,92 Q66,66 93,58"/>
    </g>
    <g font-family="Open Sans, sans-serif" font-style="italic" font-size="7.2">
      <text x="4" y="78" fill="#9a9a9a">WPS meetings</text>
      <text x="172" y="26" fill="#8fb526" font-weight="600">Weekly Peer Support</text>
      <text x="184" y="36" fill="#8fb526" font-weight="600">(WPS) meetings</text>
      <text x="194" y="46" fill="#8fb526" font-weight="600">(2 hours)</text>
      <text x="191" y="208" fill="#33a6d7" font-weight="600">WPS meetings</text>
      <text x="12" y="206" fill="#f37122" font-weight="600">WPS meetings</text>
    </g>
    <g font-family="Open Sans, sans-serif" text-anchor="middle" fill="#fff">
      <circle cx="123" cy="49" r="39" fill="#acd037"/>
      <text x="123" y="42" font-size="7">Workshop 1</text>
      <text x="123" y="56" font-size="12" font-weight="700">INSIGHT</text>
      <text x="123" y="67" font-size="6.5" font-style="italic">(5 hours)</text>

      <circle cx="209" cy="119" r="39" fill="#33a6d7"/>
      <text x="209" y="112" font-size="7">Workshop 2</text>
      <text x="209" y="126" font-size="12" font-weight="700">DESIGN</text>
      <text x="209" y="137" font-size="6.5" font-style="italic">(5 hours)</text>

      <circle cx="123" cy="187" r="39" fill="#f37122"/>
      <text x="123" y="180" font-size="7">Workshop 3</text>
      <text x="123" y="194" font-size="12" font-weight="700">EXECUTE</text>
      <text x="123" y="205" font-size="6.5" font-style="italic">(5 hours)</text>

      <circle cx="46" cy="119" r="39" fill="#a7a7a7"/>
      <text x="46" y="112" font-size="7">Workshop 4</text>
      <text x="46" y="126" font-size="12" font-weight="700">PRESENT</text>
      <text x="46" y="137" font-size="6.5" font-style="italic">(5 hours)</text>
    </g>
  </svg>

  <h2 class="abs tab tab--why">WHY</h2>
  <h2 class="abs tab tab--how">HOW</h2>
  <div class="abs how-rule"></div>

  <div class="abs col-text why-text">
    <p>Many people are not satisfied with their work or life, but they don't know what to do about it. This Program offers you a safe place to conduct your inner journey with collective support, helping you to reflect, design and do something about it. It aims at:</p>
    <ol class="steps steps--why">
      <li data-n="1">Increasing awareness, clarity and confidence</li>
      <li data-n="2">Having a deeper <b><i>insight</i></b> on what makes you happier and what you want</li>
      <li data-n="3">Developing a clear <b><i>design</i></b> integrating your intended work and life</li>
      <li data-n="4">Start <b><i>executing</i></b> this design.</li>
    </ol>
  </div>

  <div class="abs col-text how-text">
    <p>This Program differs from existing entrepreneurial programs in many ways:</p>
    <ol class="steps steps--how">
      <li data-n="1">Uses mindfulness and self analysis to look deeply into yourself</li>
      <li data-n="2">Design and execution decisions are based on happiness rather than only financials</li>
      <li data-n="3">Holistic and inclusive design process, integrating work and life, and building synergies between your different parts.</li>
    </ol>
    <p>The Program's format includes lectures, individual work, group sharing, guided activities, experiential exercises, video, audio, handouts and other resources.</p>
  </div>

  <div class="abs forest" role="img" aria-label="Photo of a person walking along a forest path between tall trees"></div>
  <div class="abs quote">the way out is in</div>
  <div class="abs quote-by">Zen Master Lien Quang</div>
  <div class="abs back-mark"></div>
  <div class="abs back-name">bright meadow</div>
  <div class="abs back-footer"><span class="dot"></span> +34 600 000 412 (video call and messaging) &nbsp;&nbsp;<span class="dot"></span> www.brightmeadow.io &nbsp;&nbsp;<span class="dot"></span> info@brightmeadow.io</div>
</section>

</body>
</html>
```